Business Card Design Project - 2 sided

We need a business card design for a card having one business on each side (ie. two businesses on one card). Would like a design that incorporates logo, tagline and normal fields (name, position, address, phone).

Would also like an allowance for small font text along the bottom (text to be determined, but less than 50 characters).

NB. Attached logo for Harbor Quill has two variations - either can be used.

www.harborquill-example.com / www.velmaro-example.com

```html
<!DOCTYPE html>
<html lang="en">
<head>
<meta charset="utf-8">
<title>Harbor Quill / Velmaro — Business Card</title>
<link rel="stylesheet" href="https://fonts.googleapis.com/css2?family=Open+Sans:wght@400;600;700&display=swap">
<style>
  :root {
    --backdrop: #4a2c17;
    --card-white: #ffffff;
    --green: #8cc63f;
    --green-deep: #6c9f36;
    --navy: #2b2a6b;
    --sky: #3a8cc8;
    --ink: #3a3a3a;
    --on-green: #ffffff;
  }
  * { box-sizing: border-box; margin: 0; padding: 0; }
  html, body { width: 1200px; height: 412px; overflow: hidden; }
  body {
    background: var(--backdrop);
    font-family: "Open Sans", Arial, sans-serif;
    position: relative;
  }
  .card {
    position: absolute;
    top: 64px;
    width: 497px;
    height: 284px;
    background: var(--card-white);
    overflow: hidden;
  }
  .card--harbor { left: 75px; }
  .card--velmaro { left: 629px; }
  .card__panel {
    position: absolute;
    inset: 0;
    width: 100%;
    height: 100%;
  }
  .brand {
    position: absolute;
    left: 0;
    width: 285px;
    text-align: center;
  }
  .brand__name {
    display: inline-flex;
    align-items: center;
    gap: 8px;
    font-size: 24px;
    font-weight: 600;
    letter-spacing: 1px;
  }
  .brand__dot {
    width: 14px; height: 14px; border-radius: 50%;
    display: inline-block;
  }
  .brand__tagline {
    margin-top: 8px;
    font-size: 9.5px;
    color: var(--ink);
  }
  .card--harbor .brand { top: 112px; }
  .card--harbor .brand__name { color: var(--navy); }
  .card--harbor .brand__dot { background: var(--green); }
  .card--velmaro .brand { top: 118px; }
  .card--velmaro .brand__name { color: var(--sky); font-size: 30px; }
  .card--velmaro .brand__dot { background: var(--green); width: 20px; height: 20px; }
  .card--velmaro .brand__tagline { font-size: 12.5px; font-weight: 700; margin-top: 4px; }

  .contact {
    position: absolute;
    left: 315px;
    top: 44px;
    color: var(--on-green);
    font-size: 12px;
    line-height: 16.5px;
  }
  .contact__name { font-size: 16px; font-weight: 700; margin-bottom: 8px; }
  .contact__title { font-size: 12px; font-weight: 400; }
  .contact__list { list-style: none; }
  .contact__list li { display: flex; align-items: center; gap: 4px; }
  .contact__icon { width: 10px; height: 10px; fill: var(--on-green); flex: none; }
  .contact__address { margin-top: 10px; }
  .contact__note { margin-top: 12px; font-size: 10.5px; line-height: 14px; letter-spacing: 0.2px; }
</style>
</head>
<body>

<svg width="0" height="0" style="position:absolute" aria-hidden="true">
  <symbol id="icon-phone" viewBox="0 0 10 10"><path d="M2 1 L4 1 L4.5 3 L3.3 3.8 C3.8 5 4.9 6.2 6.2 6.7 L7 5.5 L9 6 L9 8 C9 8.6 8.6 9 8 9 C4.5 9 1 5.5 1 2 C1 1.4 1.4 1 2 1Z"/></symbol>
  <symbol id="icon-mobile" viewBox="0 0 10 10"><path d="M3 0.5 H7 A1 1 0 0 1 8 1.5 V8.5 A1 1 0 0 1 7 9.5 H3 A1 1 0 0 1 2 8.5 V1.5 A1 1 0 0 1 3 0.5Z M3 2 V7 H7 V2Z"/></symbol>
  <symbol id="icon-fax" viewBox="0 0 10 10"><path d="M1 4 H9 V8 H1Z M3 1 H7 V4 H3Z M2.5 6 H7.5 V7 H2.5Z"/></symbol>
  <symbol id="icon-mail" viewBox="0 0 10 10"><path d="M0.5 2 H9.5 V8 H0.5Z M1 2.5 L5 5.5 L9 2.5" stroke="#8cc63f" stroke-width="0.8"/></symbol>
  <symbol id="icon-web" viewBox="0 0 10 10"><circle cx="5" cy="5" r="4.3"/><path d="M0.7 5 H9.3 M5 0.7 C3 3 3 7 5 9.3 M5 0.7 C7 3 7 7 5 9.3" stroke="#8cc63f" stroke-width="0.7" fill="none"/></symbol>
  <linearGradient id="velmaro-green" x1="0" x2="1" y1="0" y2="0">
    <stop offset="0" stop-color="#8cc63f"/>
    <stop offset="1" stop-color="#6c9f36"/>
  </linearGradient>
</svg>

<section class="card card--harbor" aria-label="Harbor Quill side">
  <svg class="card__panel" viewBox="0 0 497 284" preserveAspectRatio="none" aria-hidden="true">
    <path d="M282 0 C305 40 305 90 282 150 C262 200 250 240 258 284 L497 284 L497 0Z" fill="var(--green)"/>
    <path d="M282 0 C305 40 305 90 282 150 C262 200 250 240 258 284" fill="none" stroke="var(--navy)" stroke-width="4"/>
    <path d="M290 0 C313 40 313 90 290 150 C270 200 258 240 266 284" fill="none" stroke="#ffffff" stroke-width="2"/>
  </svg>
  <div class="brand">
    <div class="brand__name"><span class="brand__dot"></span>Harbor Quill</div>
    <p class="brand__tagline">Website Translation and Localisation Specialist...</p>
  </div>
  <div class="contact">
    <p class="contact__name">Your Name <span class="contact__title">/ Title</span></p>
    <ul class="contact__list">
      <li><svg class="contact__icon"><use href="#icon-phone"/></svg>123-456-7890</li>
      <li><svg class="contact__icon"><use href="#icon-mobile"/></svg>123-456-7890</li>
      <li><svg class="contact__icon"><use href="#icon-fax"/></svg>123-456-7890</li>
      <li><svg class="contact__icon"><use href="#icon-mail"/></svg>name@website.com</li>
      <li><svg class="contact__icon"><use href="#icon-web"/></svg>www.website.com</li>
    </ul>
    <p class="contact__address">Complex name, Street name<br>City, State, zip code</p>
    <p class="contact__note">xxxxxxxxxxxxxxxxxxxxxxxxx<br>xxxxxxxxxxxxxxxxxxxxxxxxx</p>
  </div>
</section>

<section class="card card--velmaro" aria-label="Velmaro side">
  <svg class="card__panel" viewBox="0 0 497 284" preserveAspectRatio="none" aria-hidden="true">
    <path d="M282 0 C305 40 305 90 282 150 C262 200 250 240 258 284 L497 284 L497 0Z" fill="url(#velmaro-green)"/>
    <path d="M282 0 C305 40 305 90 282 150 C262 200 250 240 258 284" fill="none" stroke="var(--sky)" stroke-width="4"/>
    <path d="M290 0 C313 40 313 90 290 150 C270 200 258 240 266 284" fill="none" stroke="#ffffff" stroke-width="2"/>
  </svg>
  <div class="brand">
    <div class="brand__name"><span class="brand__dot"></span>Velmaro LLC</div>
    <p class="brand__tagline">Professional SEO Services</p>
  </div>
  <div class="contact">
    <p class="contact__name">Your Name <span class="contact__title">/ Title</span></p>
    <ul class="contact__list">
      <li><svg class="contact__icon"><use href="#icon-phone"/></svg>123-456-7890</li>
      <li><svg class="contact__icon"><use href="#icon-mobile"/></svg>123-456-7890</li>
      <li><svg class="contact__icon"><use href="#icon-fax"/></svg>123-456-7890</li>
      <li><svg class="contact__icon"><use href="#icon-mail"/></svg>name@website.com</li>
      <li><svg class="contact__icon"><use href="#icon-web"/></svg>www.website.com</li>
    </ul>
    <p class="contact__address">Complex name, Street name<br>City, State, zip code</p>
    <p class="contact__note">xxxxxxxxxxxxxxxxxxxxxxxxx<br>xxxxxxxxxxxxxxxxxxxxxxxxx</p>
  </div>
</section>

</body>
</html>
```